Silver Kite Venture Series Travel Brochure

I'm looking for a brochure design for a new travel product - Silver Kite Venture Series, catering for students above 12 years old. Target audience are schools that do destination projects. Brochure to be read by head teacher, parents and students.

Brochure should be A4 in size, 4-6 pages. Format of brochure is hard cover (a folder) with inlet for flyers. Flyers for destinations will be updated from time to time.

Finished job needs to be converted to electronic format for website and email proposal usage.

Attached is text to be used on brochure. Order of section can be adjusted.

For "Elements of the trip", please understand the contents and explain/display it in a graphic form.

For flyer, please come out with a template that I can use for other destinations. The main elements - what's included, number of days, location for pictures, itinerary, educational focus, should be alterable. Attached are text for two sample destinations.
Also attached (tour itinerary example) a version of flyer that I like.

I'm attaching some pictures here. If you find more suitable pictures, please feel free to use them.

Reason: I'm extending the deadline of this project by 4 days, as I need to add details & photo of another travel specialist in personnel session (total of 3 members). Also, in view of the amount of work a designer has to do for this project, I'm giving you more time for submission. Please do not hesitate to be in touch should you need more than 4 days extension. Thank you.

Target Market(s)

Schools - especially the head teacher and parents, to send students above 12 years old to travel

Industry/Entity Type

Electronic

Requirements
Must have
• This is a travel brochure with education elements in it. Parents feel better when their children are travelling for a purpose and lead by responsible teachers/adults whom they can trust. So, the design has to emphasis that education elements and safety are our utmost priority.
Nice to have
• We specialise in environmental study. So, it is nice to have the environmental touch in the design.
Should not have
• Our target market segment is the Middle East, which can be quite sensitive to religion. I prefer not to have any religious related illustration on the design.

```html
<!DOCTYPE html>
<html lang="en">
<head>
<meta charset="utf-8">
<title>Silver Kite Venture Series – Destination Flyers</title>
<link rel="stylesheet" href="https://fonts.googleapis.com/css2?family=Source+Sans+3:wght@400;600;700&family=Arvo:wght@700&display=swap">
<style>
:root{
  --backdrop:#cfcfcf;
  --paper:#ffffff;
  --leaf:#8cc63f;
  --leaf-dark:#1d8a3c;
  --sky:#4f9bd6;
  --title-blue:#2f6fb5;
  --ink:#333333;
  --white:#ffffff;
}
*{box-sizing:border-box;margin:0;padding:0}
html,body{width:1200px;height:3000px;overflow:hidden}
body{background:var(--backdrop);font-family:"Source Sans 3",Arial,sans-serif;color:var(--ink);position:relative}

.page{position:absolute;left:73px;width:987px;background:var(--paper);overflow:hidden}
.page--one{top:73px;height:1367px}
.page--two{top:1533px;height:1400px}
.page-number{position:absolute;left:1088px;font-size:60px;line-height:1;color:#222;font-weight:400}

.masthead{position:absolute;left:34px;top:26px;right:40px;display:flex;align-items:flex-start}
.brand{display:flex;align-items:center;gap:8px;color:var(--title-blue);font-weight:600;font-size:17px;line-height:1;margin-top:14px}
.brand-mark{width:18px;height:18px;background:var(--title-blue)}
.series-title{font-size:44px;color:var(--title-blue);font-weight:400;line-height:1;margin-left:auto;margin-top:6px}

.destination{position:absolute;left:34px;width:903px;display:grid;grid-template-columns:310px 593px;grid-template-rows:var(--itin) var(--focus) var(--incl)}
.destination__photo{grid-column:1;grid-row:1 / 3;border-right:6px solid var(--leaf);display:flex;flex-direction:column;justify-content:flex-end;align-items:center;text-align:center;padding:0 10px 62px;color:var(--white)}
.destination__label{font-size:26px;font-weight:600;line-height:1.1}
.destination__name{font-family:"Arvo",Georgia,serif;font-size:42px;line-height:1.05;text-transform:uppercase}
.photo--borneo{background:linear-gradient(180deg,#8fb1cf 0%,#6a8b70 45%,#2f5a2a 100%)}
.photo--greece{background:linear-gradient(180deg,#3b78c2 0%,#9fb2c4 40%,#c8bfa9 100%)}
.photo--egypt{background:linear-gradient(180deg,#9ab2c4 0%,#b89a6e 45%,#8a6a42 100%)}

.itinerary{grid-column:2;grid-row:1;background:var(--leaf);color:var(--white);display:grid;grid-template-columns:1fr 1fr;gap:0 24px;padding:44px 22px 12px;font-size:13px;line-height:16px;overflow:hidden}
.itinerary dt{font-weight:700;margin-top:2px}
.focus{grid-column:2;grid-row:2;background:var(--sky);color:var(--white);display:grid;grid-template-columns:1fr 1fr;gap:24px;padding:14px 22px;overflow:hidden}
.focus h3{font-size:23px;font-weight:700;line-height:1.1}
.focus p{font-size:16px;font-weight:600;line-height:1.2;margin-bottom:5px}
.included{grid-column:2;grid-row:3;border-left:6px solid var(--leaf);padding:10px 22px 6px 16px;overflow:hidden}
.included h3{color:var(--leaf-dark);font-size:23px;font-weight:700;line-height:1.2;margin-bottom:4px}
.included ul{list-style:none;display:grid;grid-template-columns:1fr 1fr;gap:0 24px;font-size:15px;line-height:19px}

.closing{position:absolute;left:90px;right:90px;top:920px;text-align:center;color:var(--title-blue);font-size:24px;line-height:1.45}
.contact{position:absolute;left:34px;top:1262px;font-size:12px;line-height:1.35;color:#222;font-style:normal}
.contact strong{font-weight:700}
.icons{position:absolute;right:40px;top:1305px;display:flex;gap:12px;align-items:center}
.icons svg{display:block}
</style>
</head>
<body>

<section class="page page--one">
  <header class="masthead">
    <div class="brand"><span class="brand-mark"></span>Harbor Lane Consulting</div>
    <h1 class="series-title">Silver Kite Venture Series</h1>
  </header>

  <article class="destination" style="top:127px;--itin:262px;--focus:200px;--incl:116px">
    <div class="destination__photo photo--borneo" role="img" aria-label="Photograph of a mountain rising above Borneo rainforest">
      <p class="destination__label">Destination 1</p>
      <h2 class="destination__name">Malaysia<br>Borneo</h2>
    </div>
    <dl class="itinerary">
      <div>
        <dt>Day 1</dt><dd>Arrival at Kota Kinabalu<br>Cultural performance dinner</dd>
        <dt>Day 2</dt><dd>Kiulu river rafting<br>Village visit</dd>
        <dt>Day 3</dt><dd>Kinabalu Park trekking<br>Poring Hot Spring visit</dd>
        <dt>Day 4</dt><dd>Sabah tea visit<br>Sukau Rainforest wildlife cruise</dd>
      </div>
      <div>
        <dt>Day 5</dt><dd>Sepilok Orang Utan Rehabilitation Centre visit<br>Sandakan city tour</dd>
        <dt>Day 6</dt><dd>Fly to Kuala Lumpur<br>City tour<br>School visit (optional)</dd>
        <dt>Day 7</dt><dd>Departure</dd>
      </div>
    </dl>
    <div class="focus">
      <div><h3>Main focus subject</h3><p>Environmental Management</p><h3>Related subjects</h3><p>Geography, Development Studies, Agriculture, Physical Education</p></div>
      <div><h3>Environmental focus</h3><p>Biodiversity of Malaysian rainforests and conservation projects.</p></div>
    </div>
    <div class="included">
      <h3>What’s included in price:</h3>
      <ul><li>Air ticket</li><li>Meals</li><li>All accommodation</li><li>Tours led by local expert tour guides</li><li>Full time tour director</li><li>Entrance fees to attractions</li></ul>
    </div>
  </article>

  <article class="destination" style="top:760px;--itin:262px;--focus:184px;--incl:116px">
    <div class="destination__photo photo--greece" role="img" aria-label="Photograph of ancient stone columns against a blue sky">
      <p class="destination__label">Destination 2</p>
      <h2 class="destination__name">Greece</h2>
    </div>
    <dl class="itinerary">
      <div>
        <dt>Day 1</dt><dd>Arrival at Athens<br>Athens city tour</dd>
        <dt>Day 2</dt><dd>Athens to Mykonos on cruise<br>Mykonos tour</dd>
        <dt>Day 3</dt><dd>Mykonos to Kusadasi (Turkey) on cruise<br>Kusadasi tour</dd>
        <dt>Day 4</dt><dd>Kusadasi to Santorini on cruise<br>Santorini and volcano tour</dd>
      </div>
      <div>
        <dt>Day 5</dt><dd>Santorini to Athens on cruise<br>Athens second city tour</dd>
        <dt>Day 6</dt><dd>Athens to Delphi by coach (2 hours)<br>Visit hill towns on way<br>Delphi tour</dd>
        <dt>Day 7</dt><dd>Departure</dd>
      </div>
    </dl>
    <div class="focus">
      <div><h3>Main focus subject</h3><p>Geography</p><h3>Related subjects</h3><p>History, Anthropology, Environmental Management, Art and Design</p></div>
      <div><h3>Environmental focus</h3><p>Marine ecology and related human threats.</p></div>
    </div>
    <div class="included">
      <h3>What’s included in price:</h3>
      <ul><li>Air ticket</li><li>Meals</li><li>All accommodation</li><li>Tours led by local expert tour guides</li><li>Full time tour director</li><li>Entrance fees to attractions</li></ul>
    </div>
  </article>
</section>
<span class="page-number" style="top:1395px">1</span>

<section class="page page--two">
  <article class="destination" style="top:134px;--itin:300px;--focus:200px;--incl:116px">
    <div class="destination__photo photo--egypt" role="img" aria-label="Photograph of a desert pyramid under a pale sky">
      <p class="destination__label">Destination 3</p>
      <h2 class="destination__name">Egypt</h2>
    </div>
    <dl class="itinerary">
      <div>
        <dt>Day 1</dt><dd>Arrival at Cairo<br>Cairo city tour<br>Pyramid and Sphinx</dd>
        <dt>Day 2</dt><dd>Cairo Museum &amp; Khan El Khalili Bazaar<br>Cairo to Aswan by flight or train</dd>
        <dt>Day 3</dt><dd>Embark on Nile Cruise<br>Visit high dam, unfinished obelisk, Philae Temple</dd>
        <dt>Day 4</dt><dd>Nile Cruise<br>Visit temples of Kom Ombo and Edfu</dd>
      </div>
      <div>
        <dt>Day 5</dt><dd>Nile Cruise<br>Visit Temple of Karnak and Temple of Luxor</dd>
        <dt>Day 6</dt><dd>Disembark from Nile Cruise – visit Luxor Colossi of Memnon, Valley of the Kings</dd>
        <dt>Day 7</dt><dd>Luxor visit Colossi of Memnon<br>Luxor to Cairo by train</dd>
        <dt>Day 8</dt><dd>Departure</dd>
      </div>
    </dl>
    <div class="focus">
      <div><h3>Main focus subject</h3><p>History and Anthropology</p><h3>Related subjects</h3><p>Geography, Development Studies, Agriculture, Environmental Management</p></div>
      <div><h3>Environmental focus</h3><p>Impact of climate change on the Nile river basin.</p></div>
    </div>
    <div class="included">
      <h3>What’s included in price:</h3>
      <ul><li>Air ticket</li><li>Meals</li><li>All accommodation</li><li>Tours led by local expert tour guides</li><li>Full time tour director</li><li>Entrance fees to attractions</li></ul>
    </div>
  </article>

  <p class="closing">Above are some of our more popular destinations.<br>With our vast knowledge and expertise in the Middle East, Asia and Europe destinations, we are able to cater for other countries not mentioned.<br>We are constantly expanding our radar to new destinations. Upcoming destinations are Vietnam, Cambodia and Namibia.</p>

  <address class="contact">
    <strong>Harbor Lane Travel</strong><br>
    4 Palm Court Offices, Marina Row,<br>
    PO Box 100200, Sample City<br>
    <strong>Tel:</strong> +000 1 2345678<br>
    <strong>Fax:</strong> +000 1 2345679<br>
    <strong>Email:</strong> hello@harborlane.example
  </address>

  <div class="icons" aria-hidden="true">
    <svg width="60" height="26"><rect width="60" height="26" fill="#222"/></svg>
    <svg width="30" height="26"><rect y="10" width="30" height="12" fill="var(--leaf-dark)"/><rect y="4" width="4" height="22" fill="var(--leaf-dark)"/></svg>
    <svg width="30" height="30"><circle cx="15" cy="7" r="6" fill="#222"/><rect x="9" y="14" width="12" height="16" fill="#222"/></svg>
    <svg width="30" height="30"><circle cx="15" cy="15" r="12" fill="none" stroke="var(--leaf-dark)" stroke-width="4"/></svg>
    <svg width="30" height="30"><rect x="6" y="6" width="18" height="18" fill="var(--leaf)"/></svg>
    <svg width="48" height="26"><rect width="48" height="26" fill="var(--leaf-dark)"/></svg>
  </div>
</section>
<span class="page-number" style="top:2870px">2</span>

</body>
</html>
```